The Linen Loft Co

We need a business card design for our wardrobe company.
Please visit our website www.gentlelinenlofts.com to get an idea of who we are.

```html
<!DOCTYPE html>
<html lang="en">
<head>
<meta charset="UTF-8">
<title>The Linen Loft Co – Business Card</title>
<link href="https://fonts.googleapis.com/css2?family=Lato:wght@400;700&display=swap" rel="stylesheet">
<style>
  :root {
    --backdrop: #6e4328;
    --card-dark: #252223;
    --card-light: #ffffff;
    --ink: #1c1c1c;
    --ink-soft: #555555;
    --rule: #6a6a6a;
    --on-dark: #ffffff;
  }
  * { margin: 0; padding: 0; box-sizing: border-box; }
  html, body {
    width: 1200px; height: 960px; overflow: hidden;
    background: var(--backdrop);
    font-family: 'Lato', sans-serif;
  }
  .stage { position: relative; width: 1200px; height: 960px; }
  .card {
    position: absolute; left: 270px; width: 660px; height: 377px;
    border-radius: 22px;
    box-shadow: 4px 6px 12px rgba(0,0,0,0.45);
  }
  .card-front { top: 73px; background: var(--card-dark); }
  .card-back { top: 509px; background: var(--card-light); }

  .front-wordmark {
    position: absolute; left: 0; right: 0; top: 160px;
    text-align: center; color: var(--on-dark);
    font-weight: 700; font-size: 44px; letter-spacing: 1px;
  }

  .brand-square {
    position: absolute; left: 110px; top: 176px;
    width: 26px; height: 26px; background: var(--ink);
  }
  .brand-text {
    position: absolute; left: 148px; top: 172px;
    width: 164px; text-align: center;
  }
  .brand-name {
    font-size: 12.5px; font-weight: 400; color: var(--ink);
    letter-spacing: 0.4px; text-transform: uppercase; line-height: 14px;
    text-align: left;
  }
  .brand-tagline {
    font-size: 12px; font-weight: 700; color: var(--ink);
    line-height: 14px; margin-top: 6px;
  }

  .divider {
    position: absolute; left: 329px; top: 130px;
    width: 2px; height: 117px; background: var(--rule);
  }

  .person { position: absolute; left: 353px; top: 127px; }
  .person-name { font-size: 20px; font-weight: 700; color: var(--ink); line-height: 1.2; }
  .person-role { font-size: 15px; color: var(--ink-soft); line-height: 1.2; }

  .contacts { position: absolute; left: 353px; top: 189px; list-style: none; }
  .contacts li {
    display: flex; align-items: center; gap: 9px;
    font-size: 14.5px; color: var(--ink-soft); height: 19.5px;
  }
  .contacts svg { width: 11px; height: 11px; flex: none; }

  .address {
    position: absolute; left: 0; right: 0; top: 314px;
    text-align: center; font-size: 14.5px; color: var(--ink-soft);
  }
</style>
</head>
<body>
<div class="stage">
  <section class="card card-front">
    <div class="front-wordmark">The Linen Loft Co</div>
  </section>

  <section class="card card-back">
    <div class="brand-square"></div>
    <div class="brand-text">
      <div class="brand-name">The Linen Loft Co</div>
      <div class="brand-tagline">Made to Fit Every Room</div>
    </div>

    <div class="divider"></div>

    <div class="person">
      <div class="person-name">Daniel Ashworth</div>
      <div class="person-role">Managing Director</div>
    </div>

    <ul class="contacts">
      <li>
        <svg viewBox="0 0 12 12" aria-hidden="true"><path d="M2.5 1 L4.5 1 L5 3.5 L3.8 4.5 Q5 7 7.5 8.2 L8.5 7 L11 7.5 L11 9.5 Q10.5 11 9 11 Q1 10 1 3 Q1 1.5 2.5 1 Z" fill="#444"/></svg>
        0207 555 0148
      </li>
      <li>
        <svg viewBox="0 0 12 12" aria-hidden="true"><rect x="0.8" y="2" width="10.4" height="8" fill="none" stroke="#444" stroke-width="1.2"/><path d="M1 2.5 L6 6.5 L11 2.5" fill="none" stroke="#444" stroke-width="1.2"/></svg>
        info@gentlelinenlofts.com
      </li>
      <li>
        <svg viewBox="0 0 12 12" aria-hidden="true"><circle cx="6" cy="6" r="5" fill="none" stroke="#444" stroke-width="1.1"/><ellipse cx="6" cy="6" rx="2.2" ry="5" fill="none" stroke="#444" stroke-width="1"/><line x1="1" y1="6" x2="11" y2="6" stroke="#444" stroke-width="1"/></svg>
        www.gentlelinenlofts.com
      </li>
    </ul>

    <div class="address">Harrow Court, 42 Mill Lane, London EC2A 7QT</div>
  </section>
</div>
</body>
</html>
```